Web landing page design

- Create a Web Design (Uncoded - PSD layout only)

We need a single web page design to promote our service. This page will
acts as a landing page for users and also be utilized in social media
advertising. Please provide us with a cutting edge design. I have attached
a link for what the company is about. In essence we are a photo checking
service which reviews photos for retailers, hotels abd car dealerships to
check everything is good after a service has been performed. Whether it be
a new promotion, cleaning or just checking prices. I am looking for a
design to say that we do many photos and at a very cost effective price
(team based in Mexico)

Link: https://slidevault.example/view/qTr8nWx2LpZk4mHcYdJs/
*Deadline*
5 days
*Updates*

- The Start Here box needs to look like this:

-Start Here (heading)
-A box for email addresses to be entered
-Then a check box with "Yes, I have read and agree to the Privacy Policy
and agree to receive email marketing from Plumora88'
-A submit button

All of this information needs to be in one box please. And please feel
free to contact me if you have any questions about this.

*Target Market(s)*
Retail business, Merchandising companies, Rental property owners, Car
dealers
Updates

Please can you submit entries. I am just looking for a tidy to a presentation already created. Just needs design touches.

Target Market(s)

Ability for audience to understand concept quickly
Benefits to why to use the product stand out
Technology driven approach

Industry/Entity Type

Retail

Number of Pages Required

1 page

Colors
0792cd

Requirements
Must have
• Clean and modern design

```html
<!DOCTYPE html>
<html lang="en">
<head>
<meta charset="UTF-8">
<title>Checklyn – Transform Retail Execution</title>
<link rel="stylesheet" href="https://fonts.googleapis.com/css2?family=Bebas+Neue&family=Open+Sans:wght@400;600&display=swap">
<style>
  :root {
    --cyan: #00b4e4;
    --charcoal: #333333;
    --white: #ffffff;
    --ink: #222222;
    --panel: rgba(24, 22, 22, 0.82);
  }
  * { margin: 0; padding: 0; box-sizing: border-box; }
  html, body { width: 1200px; height: 857px; overflow: hidden; background: var(--white); }
  body { position: relative; font-family: "Open Sans", sans-serif; color: var(--white); }

  .hero {
    position: absolute; left: 0; top: 0; width: 1200px; height: 628px; overflow: hidden;
  }
  .hero-photo {
    position: absolute; inset: 0;
    background:
      radial-gradient(ellipse 320px 380px at 930px 360px, rgba(150,110,90,0.55), transparent 70%),
      linear-gradient(100deg, #4a4c4c 0%, #6f7470 35%, #8c8a82 55%, #5a4a42 75%, #2e2624 100%);
  }
  .hero-shade {
    position: absolute; inset: 0;
    background: linear-gradient(90deg, rgba(20,20,20,0.45) 0%, rgba(20,20,20,0.25) 55%, rgba(20,20,20,0) 80%);
  }

  .brand { position: absolute; left: 99px; top: 24px; width: 122px; text-align: center; }
  .brand-dot { width: 46px; height: 46px; border-radius: 50%; background: var(--cyan); margin: 0 auto 4px; }
  .brand-name { font-weight: 400; font-size: 34px; letter-spacing: 1px; color: var(--white); line-height: 1; }

  .main-nav { position: absolute; top: 54px; right: 99px; display: flex; gap: 56px; }
  .main-nav a {
    font-family: "Bebas Neue", sans-serif; font-size: 26px; color: var(--white);
    text-decoration: none; letter-spacing: 0.3px;
  }

  .headline {
    position: absolute; left: 99px; top: 166px; width: 600px;
    font-family: "Bebas Neue", sans-serif; font-weight: 400; font-size: 58px; line-height: 63px;
    text-shadow: 0 2px 6px rgba(0,0,0,0.35);
  }

  .signup {
    position: absolute; left: 99px; top: 315px; width: 562px; height: 252px;
    background: var(--panel); border: 3px solid var(--white); border-radius: 6px;
    padding: 18px 0 0 11px;
  }
  .signup h2 { font-family: "Bebas Neue", sans-serif; font-weight: 400; font-size: 28px; line-height: 1; }
  .email-field {
    display: block; margin-top: 22px; width: 464px; height: 43px;
    border: 2px solid var(--white); border-radius: 5px; background: transparent;
    color: var(--white); font: 600 14px "Open Sans", sans-serif; padding: 0 11px;
  }
  .email-field::placeholder { color: var(--white); }
  .consent { display: flex; gap: 12px; margin-top: 22px; width: 464px; align-items: flex-start; }
  .consent-box {
    flex: none; width: 22px; height: 22px; margin-top: 5px; border-radius: 4px;
    background: var(--white); border: none; appearance: none;
  }
  .consent-text { font-size: 14px; font-weight: 600; line-height: 21px; text-align: justify; }
  .submit {
    margin-top: 16px; width: 94px; height: 39px; border: 2px solid var(--white); border-radius: 4px;
    background: var(--cyan); color: var(--white); font: 600 15px "Open Sans", sans-serif;
  }

  .stats { position: absolute; left: 0; top: 630px; width: 1200px; height: 139px; display: flex; gap: 3px; }
  .stat { flex: 1; text-align: center; padding-top: 20px; }
  .stat--cyan { background: var(--cyan); }
  .stat--dark { background: var(--charcoal); }
  .stat-value { font-family: "Bebas Neue", sans-serif; font-size: 54px; line-height: 1; }
  .stat-label { font-size: 19px; margin-top: 12px; }

  .site-footer {
    position: absolute; left: 0; top: 806px; width: 1200px; text-align: center;
    font-size: 15px; color: var(--ink);
  }
</style>
</head>
<body>
  <section class="hero">
    <div class="hero-photo" role="img" aria-label="Photo of a smiling young woman in a street checking her smartphone while holding a coffee cup"></div>
    <div class="hero-shade"></div>

    <div class="brand">
      <div class="brand-dot"></div>
      <div class="brand-name">checklyn</div>
    </div>

    <nav class="main-nav">
      <a href="#about">About</a>
      <a href="#results">Results</a>
      <a href="#how">How</a>
      <a href="#trial">Free Trial</a>
    </nav>

    <h1 class="headline">Transform retail execution with a simple photo</h1>

    <form class="signup">
      <h2>Start Here</h2>
      <input class="email-field" type="email" placeholder="Email Address">
      <label class="consent">
        <input class="consent-box" type="checkbox">
        <span class="consent-text">"Yes, I have read and agree to the Privacy Policy and agree to receive email marketing from Plumora88'</span>
      </label>
      <button class="submit" type="button">SUBMIT</button>
    </form>
  </section>

  <section class="stats">
    <div class="stat stat--cyan"><div class="stat-value">2.2M</div><div class="stat-label">Photos reviewed last year</div></div>
    <div class="stat stat--dark"><div class="stat-value">5P</div><div class="stat-label">From per photo reviewed</div></div>
    <div class="stat stat--cyan"><div class="stat-value">97.2%</div><div class="stat-label">Average compliance</div></div>
    <div class="stat stat--dark"><div class="stat-value">3-8%</div><div class="stat-label">Sales increase</div></div>
  </section>

  <footer class="site-footer">Copyrights @ 2018 Checklyn. All Rights Reserved.</footer>
</body>
</html>
```